Tallowood building company Business card design

I need a business card design for my company. I have a logo but dont have business cards with our logo..

www.tallowoodbuildingco.com.au

The logo is on the website

I need the same details as this design I have attached. we have changed the logo and colours. just like the website

Building

```html
<!DOCTYPE html>
<html lang="en">
<head>
<meta charset="utf-8">
<title>Tallowood Building – Business Card</title>
<link href="https://fonts.googleapis.com/css2?family=Tinos&display=swap" rel="stylesheet">
<style>
  :root {
    --page: #ffffff;
    --sky: #33a7f1;
    --stone: #bcc9cb;
    --ink: #111111;
  }
  html, body {
    margin: 0;
    padding: 0;
    width: 1200px;
    height: 1000px;
    overflow: hidden;
    background: var(--page);
  }
  .canvas {
    position: relative;
    width: 1200px;
    height: 1000px;
    font-family: "Tinos", "Times New Roman", serif;
    color: var(--ink);
  }
  .card-shapes {
    position: absolute;
    left: 0;
    top: 0;
  }
  .brand-name {
    position: absolute;
    left: 106px;
    top: 380px;
    margin: 0;
    font-weight: 400;
    font-size: 40px;
    line-height: 42px;
    letter-spacing: 2px;
    color: var(--sky);
    text-transform: uppercase;
  }
  .contact-block {
    position: absolute;
    left: 110px;
    top: 503px;
    margin: 0;
    font-size: 24px;
    line-height: 33px;
    font-style: normal;
  }
  .contact-block p { margin: 0; }
  .person {
    position: absolute;
    right: 140px;
    top: 528px;
    margin: 0;
    font-weight: 400;
    font-size: 40px;
    line-height: 46px;
    text-decoration: underline;
    text-decoration-thickness: 2px;
    text-underline-offset: 8px;
  }
  .phone-block {
    position: absolute;
    right: 138px;
    top: 625px;
    margin: 0;
    font-size: 24px;
    line-height: 33px;
    text-align: right;
  }
  .phone-block p { margin: 0; }
</style>
</head>
<body>
<div class="canvas">
  <svg class="card-shapes" width="1200" height="1000" viewBox="0 0 1200 1000" aria-hidden="true">
    <path class="sky-sweep" fill="var(--sky)"
          d="M107 205 L1132 205 L1132 568 C1060 470 900 380 700 315 C520 258 300 225 107 205 Z"/>
    <path class="stone-sweep" fill="var(--stone)"
          d="M68 445 C150 560 320 630 560 690 C760 740 950 775 1078 795 L68 795 Z"/>
  </svg>

  <h1 class="brand-name">Tallowood<br>Building</h1>

  <address class="contact-block">
    <p>Address :</p>
    <p>Unit 3 Level 2,</p>
    <p>18 Marlee Cres,</p>
    <p>Joondalup, WA 6027</p>
    <p>Email&nbsp;&nbsp;&nbsp;&nbsp;&nbsp;:</p>
    <p>info@tallowoodbuildingco.com.au</p>
    <p>Web :</p>
    <p>www.tallowoodbuildingco.com.au</p>
  </address>

  <h2 class="person">Name&nbsp;</h2>

  <div class="phone-block">
    <p>Phone :</p>
    <p>9312 4470</p>
    <p>Mob&nbsp;&nbsp;&nbsp;&nbsp;:</p>
    <p>0412580963 ( Mara )</p>
  </div>
</div>
</body>
</html>
```